Birchpoint Studio Complementary Pass

I’d like a complimentary pass for any 30-minute Birchpoint Studio session. Choose one of the following options: Infrared Sauna with Red Light, Massage Chair Veltrafix Compression Therapy, or Paraffin Wax Hand Bath.

Please incorporate the logo and brand colors into your design. I’d like a square image that will be printed on square business cards (no rectangles).

Please refer to the logo and menu for more details.

Contact Information for Business Card

See discretion

```html
<!DOCTYPE html>
<html lang="en">
<head>
<meta charset="utf-8">
<title>Birchpoint Studio – Complimentary Pass</title>
<link href="https://fonts.googleapis.com/css2?family=Poppins:wght@400;500;600;700&family=Oswald:wght@500&display=swap" rel="stylesheet">
<style>
  :root {
    --stage: #2b2d31;
    --brand-purple: #4a2f96;
    --brand-orange: #ee6644;
    --card-white: #ffffff;
    --ink: #1f1f24;
    --rule: #3a3a40;
    --soft-white: rgba(255,255,255,0.82);
  }
  * { box-sizing: border-box; margin: 0; padding: 0; }
  html, body { width: 1200px; height: 985px; overflow: hidden; }
  body {
    background: var(--stage);
    font-family: "Poppins", sans-serif;
    display: flex;
    align-items: center;
    justify-content: center;
    gap: 44px;
  }
  .card {
    position: relative;
    width: 520px;
    height: 520px;
    border-radius: 28px;
    overflow: hidden;
    box-shadow: 0 18px 40px rgba(0,0,0,0.45);
  }

  /* Front side */
  .card--front { background: var(--card-white); }
  .front-shape { position: absolute; inset: 0; }
  .brand-dot {
    display: inline-block;
    width: 16px; height: 16px;
    border-radius: 50%;
    background: var(--brand-orange);
    flex: none;
  }
  .brand-name {
    position: absolute;
    left: 40px; top: 96px;
    display: flex;
    align-items: flex-start;
    gap: 12px;
  }
  .brand-name .brand-dot { margin-top: 16px; }
  .brand-word {
    font-weight: 700;
    font-size: 42px;
    line-height: 1.05;
    color: var(--brand-purple);
  }
  .front-divider {
    position: absolute;
    left: 40px; top: 226px;
    width: 290px; height: 1.5px;
    background: var(--rule);
  }
  .contact-list {
    position: absolute;
    left: 40px;
    list-style: none;
    font-size: 13px;
    color: var(--ink);
    display: flex;
    flex-direction: column;
    gap: 8px;
  }
  .contact-list--phones { top: 250px; }
  .contact-list--online { top: 370px; }
  .contact-list li { display: flex; align-items: center; gap: 9px; }
  .contact-icon { width: 16px; height: 16px; flex: none; }
  .front-split {
    position: absolute;
    left: 190px; top: 254px;
    width: 1.5px; height: 70px;
    background: var(--rule);
  }
  .holder {
    position: absolute;
    right: 30px; top: 30px;
    text-align: right;
  }
  .holder-name {
    font-weight: 600;
    font-size: 16px;
    letter-spacing: 0.5px;
    color: var(--card-white);
  }
  .holder-role {
    font-size: 12px;
    color: var(--brand-orange);
    margin-top: 2px;
  }

  /* Back side – the pass */
  .card--back {
    background: var(--brand-purple);
    color: var(--card-white);
    display: flex;
    flex-direction: column;
    align-items: center;
    justify-content: center;
    text-align: center;
    padding: 0 44px;
  }
  .pass-label {
    font-family: "Oswald", sans-serif;
    font-weight: 500;
    font-size: 17px;
    letter-spacing: 5px;
    color: var(--brand-orange);
  }
  .pass-brand {
    display: flex;
    align-items: center;
    gap: 12px;
    margin-top: 14px;
    font-weight: 700;
    font-size: 40px;
    line-height: 1;
  }
  .pass-offer {
    margin-top: 16px;
    font-family: "Oswald", sans-serif;
    font-weight: 500;
    font-size: 18px;
    letter-spacing: 4px;
  }
  .pass-rule {
    width: 90px; height: 2px;
    background: var(--brand-orange);
    margin: 22px 0 18px;
  }
  .pass-choose {
    font-size: 13px;
    color: var(--soft-white);
    margin-bottom: 12px;
  }
  .session-list {
    list-style: none;
    display: flex;
    flex-direction: column;
    gap: 10px;
    text-align: left;
  }
  .session-list li {
    display: flex;
    align-items: center;
    gap: 10px;
    font-size: 15px;
    font-weight: 500;
  }
  .tick { width: 18px; height: 18px; flex: none; }
</style>
</head>
<body>

  <section class="card card--front" aria-label="Pass front with contact details">
    <svg class="front-shape" width="520" height="520" viewBox="0 0 520 520" aria-hidden="true">
      <path d="M300 0 Q470 260 380 520 L520 520 L520 0 Z" fill="var(--brand-purple)"/>
      <path d="M282 -4 Q452 260 362 524" fill="none" stroke="var(--brand-orange)" stroke-width="6"/>
    </svg>

    <div class="holder">
      <p class="holder-name">MARCUS T HALE</p>
      <p class="holder-role">CEO</p>
    </div>

    <div class="brand-name">
      <span class="brand-dot"></span>
      <span class="brand-word">Birchpoint<br>Studio</span>
    </div>

    <div class="front-divider"></div>

    <ul class="contact-list contact-list--phones">
      <li>
        <svg class="contact-icon" viewBox="0 0 16 16" aria-hidden="true"><circle cx="8" cy="8" r="8" fill="var(--brand-orange)"/><path d="M5 4.5c.5 3 2.5 5.5 6 7l.8-1.3-1.8-1-.8.7c-1-.6-1.9-1.5-2.4-2.5l.7-.8-1-1.8z" fill="#fff"/></svg>
        (555) 210-4480
      </li>
      <li>
        <svg class="contact-icon" viewBox="0 0 16 16" aria-hidden="true"><circle cx="8" cy="8" r="8" fill="var(--brand-orange)"/><rect x="5.5" y="4" width="5" height="8" rx="1" fill="#fff"/></svg>
        (555) 210-4481
      </li>
      <li>
        <svg class="contact-icon" viewBox="0 0 16 16" aria-hidden="true"><circle cx="8" cy="8" r="8" fill="var(--brand-orange)"/><rect x="4.5" y="5" width="7" height="6" rx="1" fill="#fff"/></svg>
        (555) 210-4482
      </li>
    </ul>
    <div class="front-split"></div>

    <ul class="contact-list contact-list--online">
      <li>
        <svg class="contact-icon" viewBox="0 0 16 16" aria-hidden="true"><circle cx="8" cy="8" r="8" fill="var(--brand-orange)"/><rect x="4" y="5" width="8" height="6" fill="#fff"/><path d="M4 5l4 3.5L12 5" fill="none" stroke="var(--brand-orange)" stroke-width="1"/></svg>
        hello@birchpointstudio.com
      </li>
      <li>
        <svg class="contact-icon" viewBox="0 0 16 16" aria-hidden="true"><circle cx="8" cy="8" r="8" fill="var(--brand-orange)"/><circle cx="8" cy="8" r="4" fill="none" stroke="#fff" stroke-width="1.2"/><path d="M4 8h8M8 4v8" stroke="#fff" stroke-width="1"/></svg>
        www.birchpointstudio.com
      </li>
    </ul>
  </section>

  <section class="card card--back" aria-label="Complimentary pass">
    <p class="pass-label">COMPLIMENTARY PASS</p>
    <div class="pass-brand"><span class="brand-dot"></span>Birchpoint Studio</div>
    <p class="pass-offer">ANY 30-MINUTE SESSION</p>
    <div class="pass-rule"></div>
    <p class="pass-choose">Choose one of the following:</p>
    <ul class="session-list">
      <li>
        <svg class="tick" viewBox="0 0 18 18" aria-hidden="true"><circle cx="9" cy="9" r="9" fill="var(--brand-orange)"/><path d="M5 9.2l2.6 2.6L13 6.4" fill="none" stroke="#fff" stroke-width="2"/></svg>
        Infrared Sauna with Red Light
      </li>
      <li>
        <svg class="tick" viewBox="0 0 18 18" aria-hidden="true"><circle cx="9" cy="9" r="9" fill="var(--brand-orange)"/><path d="M5 9.2l2.6 2.6L13 6.4" fill="none" stroke="#fff" stroke-width="2"/></svg>
        Massage Chair Veltrafix Compression Therapy
      </li>
      <li>
        <svg class="tick" viewBox="0 0 18 18" aria-hidden="true"><circle cx="9" cy="9" r="9" fill="var(--brand-orange)"/><path d="M5 9.2l2.6 2.6L13 6.4" fill="none" stroke="#fff" stroke-width="2"/></svg>
        Paraffin Wax Hand Bath
      </li>
    </ul>
  </section>

</body>
</html>
```